Trinkets & Novelties: Promotional Products and Apparel- Tri fold hand out

Promotional Products / Advertising Specialties distributor with in-house manufacturing capabilities. We want to improve our Tri-Fold hand out that we use for Tradeshows and new customers.
Our old Tri-fold is attached. I don't care for the layout and much of the content, so I would use it as an example of how not to do the new tri-fold. Our business card is attached and I'd like the color scheme of the new tri-fold to match the color scheme of the business card. Our logo is attached and a word doc is attached for the content / text of the new tri-fold. Tri-fold should use a combination of pictures and text. Front cover should clearly define Promotional Products and Corporate Apparel.

Target Market(s)

Corporate Business

Industry/Entity Type

Advertising

Colors
3176b5

Requirements
Must have
• company name, phone, address, web
Nice to have
• Pics of screen printing, embroidery equipment
Should not have
• n/a

```html
<!DOCTYPE html>
<html lang="en">
<head>
<meta charset="UTF-8">
<title>Trinkets &amp; Novelties – Tri-fold Inside Spread</title>
<link href="https://fonts.googleapis.com/css2?family=Montserrat:wght@400;500;600&display=swap" rel="stylesheet">
<style>
  :root {
    --brand-blue: #3176b5;
    --bright-blue: #1e8fd6;
    --tab-blue: #2a8ed3;
    --deep-navy: #2a3f8f;
    --body-grey: #5a5a5a;
    --paper: #ffffff;
    --tick-green: #3aa935;
  }
  * { box-sizing: border-box; margin: 0; padding: 0; }
  html, body { width: 1200px; height: 800px; overflow: hidden; background: var(--paper); }
  body { font-family: "Montserrat", sans-serif; }

  .spread { position: relative; width: 1200px; height: 800px; background: var(--paper); }

  .photo-band { position: absolute; inset: 0; width: 1200px; height: 800px; }

  .panel-fold { position: absolute; top: 0; left: 400px; width: 1px; height: 800px; background: rgba(0,0,0,0.05); }

  /* Left panel */
  .about { position: absolute; left: 40px; top: 318px; width: 330px; }
  .about-title { color: var(--bright-blue); font-weight: 500; font-size: 21px; line-height: 23px; letter-spacing: 0.5px; }
  .title-rule { display: block; width: 88px; height: 4px; margin-top: 6px; background: linear-gradient(90deg, var(--deep-navy) 0 20%, var(--bright-blue) 20% 100%); }
  .about-copy { margin-top: 24px; color: var(--body-grey); font-size: 12.8px; line-height: 24px; text-align: justify; }
  .benefits { list-style: none; margin-top: 36px; }
  .benefits li { display: flex; align-items: center; gap: 12px; color: var(--bright-blue); font-size: 14px; line-height: 25px; }
  .benefits svg { flex: none; }

  /* Right panels */
  .services-head { position: absolute; left: 400px; width: 800px; top: 402px; text-align: center; }
  .services-title { display: inline-block; color: var(--brand-blue); font-weight: 500; font-size: 20px; letter-spacing: 0.3px; }
  .services-title .rule { display: block; height: 4px; margin: 6px auto 0; width: 100%; background: linear-gradient(90deg, var(--deep-navy) 0 20%, var(--bright-blue) 20% 100%); }
  .services-sub { margin-top: 10px; color: var(--brand-blue); font-size: 11.5px; font-weight: 500; }

  .service-grid { position: absolute; left: 450px; top: 492px; display: grid; grid-template-columns: repeat(3, 180px); column-gap: 75px; row-gap: 20px; }
  .service-card { width: 180px; }
  .service-label { height: 30px; background: var(--tab-blue); color: #fff; font-size: 14px; font-weight: 500; display: flex; align-items: center; justify-content: center; }
  .service-visual { height: 105px; border-radius: 0 0 90px 90px / 0 0 80px 80px; overflow: hidden; }
  .visual-screen { background: linear-gradient(135deg, #e9e4e0, #f08a3c 55%, #d9d2cc); }
  .visual-embroidery { background: linear-gradient(180deg, #8a8f94 0 30%, #3f9b4b 30% 55%, #d8262e 55%); }
  .visual-engraving { background: linear-gradient(135deg, #e3cfae, #2f8ea0 55%, #e6d6bd); }
  .visual-digital { background: linear-gradient(135deg, #3d5c86, #8a8f96 45%, #f2b63a 70%, #2b6fb8); }
  .visual-global { background: radial-gradient(circle at 45% 45%, #bfe6fa, #2c9be0 55%, #0f5fa8); }
  .visual-fulfillment { background: linear-gradient(180deg, #ffffff, #eef1f4); display: flex; align-items: center; justify-content: center; }
</style>
</head>
<body>
<main class="spread">

  <svg class="photo-band" viewBox="0 0 1200 800" xmlns="http://www.w3.org/2000/svg">
    <defs>
      <clipPath id="band-clip">
        <path d="M0,0 H1200 V352 C1150,342 1050,300 900,300 C700,300 550,370 400,390 C250,410 150,240 0,250 Z"/>
      </clipPath>
      <linearGradient id="press-tones" x1="0" y1="0" x2="1" y2="1">
        <stop offset="0" stop-color="#5d6a73"/>
        <stop offset="0.5" stop-color="#b8d64a"/>
        <stop offset="1" stop-color="#3a9a4a"/>
      </linearGradient>
      <linearGradient id="product-tones" x1="0" y1="0" x2="1" y2="1">
        <stop offset="0" stop-color="#f4f6f8"/>
        <stop offset="0.5" stop-color="#4a8fd0"/>
        <stop offset="1" stop-color="#eaf1f7"/>
      </linearGradient>
    </defs>
    <g clip-path="url(#band-clip)">
      <rect x="0" y="0" width="400" height="420" fill="url(#press-tones)" role="img" aria-label="Photo of hands pulling a squeegee across a screen printing frame"/>
      <rect x="400" y="0" width="800" height="420" fill="url(#product-tones)" role="img" aria-label="Photo of branded promotional products: tote bag, notebooks, mouse pad, pens, tumbler and keychain"/>
    </g>
    <path class="wave-band" fill="#1e8fd6"
      d="M0,250 C150,240 250,410 400,390 C550,370 700,300 900,300 C1050,300 1150,342 1200,352
         L1200,372 C1150,362 1050,318 900,318 C700,318 560,392 400,412 C250,428 150,255 0,256 Z"/>
  </svg>

  <div class="panel-fold"></div>

  <section class="about">
    <h2 class="about-title">WHO<br>WE ARE</h2>
    <span class="title-rule"></span>
    <p class="about-copy">Founded in 1983, Trinkets &amp; Novelties has been providing its customers with promotional product service excellence. International corporations, multi generational family businesses, government agencies, local schools, and small businesses have all trusted Trinkets &amp; Novelties to provide guidance, reliability and service excellence with regards to their promotional marketing needs.</p>
    <ul class="benefits">
      <li><svg width="11" height="11" viewBox="0 0 11 11"><circle cx="5.5" cy="5.5" r="4.5" fill="none" stroke="#2a3f8f" stroke-width="1.2"/><circle cx="5.5" cy="5.5" r="2" fill="#2a3f8f"/></svg>Maximize your marketing budget</li>
      <li><svg width="11" height="11" viewBox="0 0 11 11"><circle cx="5.5" cy="5.5" r="4.5" fill="none" stroke="#2a3f8f" stroke-width="1.2"/><circle cx="5.5" cy="5.5" r="2" fill="#2a3f8f"/></svg>Increase customer loyalty</li>
      <li><svg width="11" height="11" viewBox="0 0 11 11"><circle cx="5.5" cy="5.5" r="4.5" fill="none" stroke="#2a3f8f" stroke-width="1.2"/><circle cx="5.5" cy="5.5" r="2" fill="#2a3f8f"/></svg>Strengthen brand awareness</li>
    </ul>
  </section>

  <header class="services-head">
    <h2 class="services-title">IN-HOUSE SERVICES<span class="rule"></span></h2>
    <p class="services-sub">Promotional Product Selection and Delivery</p>
  </header>

  <section class="service-grid">
    <article class="service-card">
      <h3 class="service-label">Screen Printing</h3>
      <div class="service-visual visual-screen" role="img" aria-label="Photo of ink being spread on a screen printing press"></div>
    </article>
    <article class="service-card">
      <h3 class="service-label">Embroidery</h3>
      <div class="service-visual visual-embroidery" role="img" aria-label="Photo of an embroidery machine stitching a cap"></div>
    </article>
    <article class="service-card">
      <h3 class="service-label">Engraving</h3>
      <div class="service-visual visual-engraving" role="img" aria-label="Photo of hands engraving a plate with hand tools"></div>
    </article>
    <article class="service-card">
      <h3 class="service-label">Digital Print</h3>
      <div class="service-visual visual-digital" role="img" aria-label="Photo of a digital printing press"></div>
    </article>
    <article class="service-card">
      <h3 class="service-label">Fulfillment</h3>
      <div class="service-visual visual-fulfillment">
        <svg width="70" height="60" viewBox="0 0 70 60" aria-hidden="true">
          <path d="M6,32 L24,52 L64,6" fill="none" stroke="#3aa935" stroke-width="10" stroke-linecap="round" stroke-linejoin="round"/>
        </svg>
      </div>
    </article>
    <article class="service-card">
      <h3 class="service-label">Global Sourcing</h3>
      <div class="service-visual visual-global" role="img" aria-label="Illustration of a blue globe with connection lines"></div>
    </article>
  </section>

</main>
</body>
</html>
```